Northfield Builders Guild Business card

We are looking for a new business card design with photo included.
Our business is a nonprofit construction contractor membership organization. We offer business education, assist with business setup and licensing, provide safety training, and provide a member directory.
URL: www.builderslinkguild.org
Color code:
CMYK: 0 cyan, 42 magenta, 100 yellow, 0 black for Print.
Hexidecimal: #FF9900
RGB: R 255; G 153; B 0

```html
<!DOCTYPE html>
<html lang="en">
<head>
<meta charset="utf-8">
<title>Northfield Builders Guild – Business Card</title>
<link href="https://fonts.googleapis.com/css2?family=Arimo:wght@400;700&display=swap" rel="stylesheet">
<style>
  :root {
    --backdrop: #b7b7b7;
    --card: #1a1a1a;
    --orange: #ff9900;
    --white: #ffffff;
  }
  * { margin: 0; padding: 0; box-sizing: border-box; }
  html, body {
    width: 1200px; height: 801px; overflow: hidden;
    background: var(--backdrop);
    font-family: "Arimo", Arial, sans-serif;
    color: var(--white);
  }
  .stage { position: relative; width: 1200px; height: 801px; }
  .card {
    position: absolute; top: 274px;
    width: 443px; height: 263px;
    background: var(--card);
  }
  .card--front { left: 153px; }
  .card--back { left: 625px; }

  .brand-name {
    position: absolute;
    font-weight: 700; color: var(--white);
    line-height: 1.05; letter-spacing: 0.5px;
  }
  .card--front .brand-name {
    right: 35px; top: 40px; width: 240px;
    font-size: 27px; text-align: right;
  }
  .card--back .brand-name {
    left: 0; right: 0; top: 92px;
    font-size: 33px; text-align: center;
  }

  .person-name {
    position: absolute; left: 20px; top: 116px;
    font-size: 16.5px; font-weight: 700; color: var(--orange);
  }
  .person-title {
    position: absolute; left: 20px; top: 135px;
    font-size: 11px; letter-spacing: 0.2px;
  }
  .title-rule {
    position: absolute; left: 150px; top: 142px;
    width: 257px; height: 1px; background: var(--orange);
  }

  .contact-list {
    position: absolute; left: 19px; top: 165px;
    list-style: none;
  }
  .contact-list li {
    display: flex; align-items: center;
    height: 16.3px; font-size: 12.5px; white-space: nowrap;
  }
  .contact-icon {
    width: 15px; height: 15px; margin-right: 3px; flex: none;
  }

  .address {
    position: absolute; right: 35px; top: 199px;
    font-size: 12.5px; line-height: 15.6px; text-align: right;
    font-style: normal;
  }

  .services-rule {
    position: absolute; left: 38px; top: 207px;
    width: 366px; height: 1px; background: var(--orange);
  }
  .services {
    position: absolute; left: 0; right: 0; top: 213px;
    font-size: 12.5px; line-height: 15.6px; text-align: center;
  }
  .dot {
    display: inline-block; width: 6px; height: 6px; border-radius: 50%;
    background: var(--orange); margin: 0 7px; vertical-align: middle;
  }
</style>
</head>
<body>
<div class="stage">

  <section class="card card--front">
    <div class="brand-name">Northfield<br>Builders Guild</div>

    <div class="person-name">DANIEL REYES</div>
    <div class="person-title">MANAGING DIRECTOR</div>
    <div class="title-rule"></div>

    <ul class="contact-list">
      <li>
        <svg class="contact-icon" viewBox="0 0 16 16"><circle cx="8" cy="8" r="8" fill="#ff9900"/><path d="M5.2 4.2l1.4-.3.8 2-1 .8a5.5 5.5 0 0 0 2.9 2.9l.8-1 2 .8-.3 1.4c-3.6.4-7-3-6.6-6.6z" fill="#1a1a1a"/></svg>
        (555) 210-4800 (Office)
      </li>
      <li>
        <svg class="contact-icon" viewBox="0 0 16 16"><circle cx="8" cy="8" r="8" fill="#ff9900"/><rect x="5.3" y="3.5" width="5.4" height="9" rx="1" fill="#1a1a1a"/><rect x="6.2" y="4.6" width="3.6" height="5.6" fill="#ff9900"/></svg>
        800-555-0142
      </li>
      <li>
        <svg class="contact-icon" viewBox="0 0 16 16"><circle cx="8" cy="8" r="8" fill="#ff9900"/><rect x="5.5" y="3.6" width="5" height="2.6" fill="#1a1a1a"/><rect x="4" y="6.6" width="8" height="4" rx="0.8" fill="#1a1a1a"/><rect x="5.5" y="9.4" width="5" height="3" fill="#1a1a1a" stroke="#ff9900" stroke-width="0.6"/></svg>
        555.318.0927
      </li>
      <li>
        <svg class="contact-icon" viewBox="0 0 16 16"><circle cx="8" cy="8" r="8" fill="#ff9900"/><rect x="3.8" y="5" width="8.4" height="6" fill="#1a1a1a"/><path d="M3.8 5l4.2 3.4L12.2 5" fill="none" stroke="#ff9900" stroke-width="0.8"/></svg>
        hello@nbguild.org
      </li>
      <li>
        <svg class="contact-icon" viewBox="0 0 16 16"><circle cx="8" cy="8" r="8" fill="#ff9900"/><g fill="none" stroke="#1a1a1a" stroke-width="0.8"><circle cx="8" cy="8" r="4.3"/><ellipse cx="8" cy="8" rx="1.9" ry="4.3"/><path d="M3.7 8h8.6M4.3 6h7.4M4.3 10h7.4"/></g></svg>
        www.builderslinkguild.org
      </li>
    </ul>

    <address class="address">
      2400 Ridgeline Ave<br>
      Suite #210, Northfield<br>
      MN 55057
    </address>
  </section>

  <section class="card card--back">
    <div class="brand-name">Northfield<br>Builders Guild</div>
    <div class="services-rule"></div>
    <p class="services">
      Business education<span class="dot"></span>Assist with business setup and licensing<br>
      Provide safety training<span class="dot"></span>Provide a member directory
    </p>
  </section>

</div>
</body>
</html>
```